Kestrel Facilities Business Card Design

We would now like to design business cards with the new Kestrel Facilities logo

Target Market(s)

Professional

Industry/Entity Type

Professional services

Contact Information for Business Card

Employee name, title, phone number, email address, corporate office address and logo.

Font styles to use
Sans Serif

Colors
0054AA
0677BA
7BADD7
CADEEF
E8F1F8

Requirements
Must have
• My logo
Should not have
• any other pictures or images besides my logo

```html
<!DOCTYPE html>
<html lang="en">
<head>
<meta charset="utf-8">
<title>Kestrel Facilities Business Card</title>
<link href="https://fonts.googleapis.com/css2?family=Montserrat:wght@400;500;700&display=swap" rel="stylesheet">
<style>
  :root {
    --brand-blue: #3479c1;
    --deep-blue: #0054AA;
    --ink: #1d1d1f;
    --paper: #ffffff;
    --backdrop: #d8dbe0;
  }
  * { box-sizing: border-box; margin: 0; padding: 0; }
  html, body { width: 1200px; height: 900px; overflow: hidden; }
  body {
    background: var(--backdrop);
    font-family: "Montserrat", sans-serif;
    position: relative;
  }
  .card {
    position: absolute;
    left: 250px;
    width: 700px;
    height: 400px;
    background: var(--paper);
    border-radius: 30px;
    overflow: hidden;
    box-shadow: 0 6px 18px rgba(0,0,0,0.18);
  }
  .card--front { top: 30px; }
  .card--back { top: 470px; }

  .wordmark {
    color: var(--brand-blue);
    font-weight: 700;
    letter-spacing: 0.02em;
    display: flex;
    align-items: center;
    gap: 14px;
    white-space: nowrap;
  }
  .wordmark__square {
    width: 26px; height: 26px;
    background: var(--brand-blue);
  }
  .card--front .wordmark {
    position: absolute;
    left: 50%; top: 50%;
    transform: translate(-50%, -50%);
    font-size: 40px;
  }

  .card__swoosh { position: absolute; inset: 0; width: 100%; height: 100%; }
  .card__swoosh path { fill: var(--brand-blue); }

  .card--back .wordmark {
    position: absolute;
    left: 190px; top: 100px;
    font-size: 32px;
  }
  .person {
    position: absolute;
    right: 400px; top: 200px;
    text-align: right;
  }
  .person__name {
    color: var(--brand-blue);
    font-weight: 700;
    font-size: 26px;
    letter-spacing: 0.01em;
  }
  .person__title {
    color: var(--ink);
    font-size: 17px;
    margin-top: 4px;
  }
  .divider {
    position: absolute;
    left: 318px; top: 180px;
    width: 2px; height: 92px;
    background: var(--brand-blue);
  }
  .contacts {
    position: absolute;
    left: 338px; top: 180px;
    list-style: none;
  }
  .contacts li {
    display: flex;
    align-items: center;
    gap: 10px;
    font-size: 17px;
    color: var(--ink);
    height: 30px;
  }
  .contacts svg { width: 18px; height: 18px; fill: var(--brand-blue); }
  .address {
    position: absolute;
    left: 0; right: 0; top: 292px;
    text-align: center;
    font-size: 17px;
    color: var(--ink);
  }
</style>
</head>
<body>
  <section class="card card--front">
    <div class="wordmark"><span class="wordmark__square"></span>Kestrel Facilities</div>
  </section>

  <section class="card card--back">
    <svg class="card__swoosh" viewBox="0 0 700 400" preserveAspectRatio="none" aria-hidden="true">
      <path d="M390 0 H700 V130 C640 60 520 50 390 0 Z"/>
      <path d="M0 255 C90 340 260 380 470 400 H0 Z"/>
    </svg>
    <div class="wordmark"><span class="wordmark__square"></span>Kestrel Facilities</div>

    <div class="person">
      <div class="person__name">DANA WHITLOCK</div>
      <div class="person__title">Co-Founder</div>
    </div>

    <div class="divider"></div>

    <ul class="contacts">
      <li>
        <svg viewBox="0 0 24 24"><path d="M6.6 10.8a15.1 15.1 0 0 0 6.6 6.6l2.2-2.2a1 1 0 0 1 1-.25 11.4 11.4 0 0 0 3.6.57 1 1 0 0 1 1 1V20a1 1 0 0 1-1 1A17 17 0 0 1 3 4a1 1 0 0 1 1-1h3.5a1 1 0 0 1 1 1c0 1.25.2 2.45.57 3.6a1 1 0 0 1-.25 1z"/></svg>
        +254-150-55512
      </li>
      <li>
        <svg viewBox="0 0 24 24"><path d="M2 5h20v14H2z M4 7v.5l8 5 8-5V7l-8 5z" fill-rule="evenodd"/></svg>
        info@kestrelfm.com
      </li>
      <li>
        <svg viewBox="0 0 24 24"><circle cx="12" cy="12" r="10"/><path d="M2 12h20M12 2c3 3 3 17 0 20M12 2c-3 3-3 17 0 20" stroke="#fff" stroke-width="1.4" fill="none"/></svg>
        www.kestrelfm.com
      </li>
    </ul>

    <p class="address">4180 N. Harbor Lane Suite 210 Eastfield 12</p>
  </section>
</body>
</html>
```